Real Estate Brokerage Stationery Designs

I am looking to have presentation folders with business card slots on both sides along with pockets on both sides. I've attached logos, website colors along with current business card designs.

I am looking for envelope designs both big and small. Possibly new business card designs, notepad templates for big and small notepads. Letterhead designs. Pop socket designs. Realtors name badge designs.

www.brightholdrealty.example

```html
<!DOCTYPE html>
<html lang="en">
<head>
<meta charset="utf-8">
<title>Brighthold Realty Stationery</title>
<link href="https://fonts.googleapis.com/css2?family=Open+Sans:wght@400;600&family=Tinos&display=swap" rel="stylesheet">
<style>
  :root{
    --stage:#555555;
    --brand-blue:#0055a5;
    --band-gray:#a9a9a9;
    --paper-light:#f5f5f5;
    --paper-dark:#e1e1e1;
    --ink:#4a4a4a;
    --ink-soft:#5c5c5c;
  }
  *{margin:0;padding:0;box-sizing:border-box}
  html,body{width:1200px;height:871px;overflow:hidden;background:var(--stage)}
  .canvas{position:relative;width:1200px;height:871px}
  .sheet{position:absolute;background:linear-gradient(90deg,var(--paper-light),var(--paper-dark));box-shadow:0 1px 3px rgba(0,0,0,.35);overflow:hidden}
  .band-top{position:absolute;left:0;top:0;width:100%;background:var(--band-gray)}
  .band-bottom{position:absolute;left:0;bottom:0;width:100%;background:var(--brand-blue)}
  .brand-name{font-family:"Open Sans",sans-serif;font-weight:600;color:var(--brand-blue);white-space:nowrap;text-align:center}

  /* envelope front */
  .envelope-front{left:54px;top:216px;width:560px;height:256px}
  .envelope-front .band-top{height:7px}
  .envelope-front .band-bottom{height:8px;bottom:2px}
  .envelope-front .brand-name{position:absolute;left:20px;top:300px}
  .envelope-front .return-brand{position:absolute;left:25px;top:90px;width:120px;font-size:15px;line-height:18px}
  .return-address{position:absolute;left:25px;top:124px;width:120px;font-family:"Open Sans",sans-serif;font-size:7px;line-height:9.5px;color:var(--ink);text-align:center}

  /* envelope back */
  .envelope-back{left:54px;top:500px;width:560px;height:254px}
  .envelope-back .flap{position:absolute;left:0;top:0}
  .flap-brand{position:absolute;left:0;top:36px;width:560px;font-family:"Open Sans",sans-serif;font-weight:600;font-size:16px;color:#ffffff;text-align:center}

  /* letterhead */
  .letterhead{left:639px;top:58px;width:521px;height:734px}
  .letterhead .band-top{height:7px}
  .letterhead .band-bottom{height:8px}
  .letterhead .masthead{position:absolute;left:0;top:110px;width:100%;font-size:17px}
  .letter{position:absolute;left:47px;width:432px;font-family:"Tinos",serif;color:var(--ink-soft)}
  .letter-date{top:178px;font-size:9px}
  .letter-recipient{top:214px;font-size:9px;line-height:12px}
  .letter-body{top:288px;font-size:8px;line-height:12px;text-align:justify}
  .letter-body p{margin-bottom:12px}
  .signature-area{position:absolute;left:51px;top:526px;width:106px;height:40px;background:linear-gradient(90deg,rgba(90,90,90,.18),rgba(90,90,90,.06));border-radius:3px}
  .contact-list{position:absolute;left:66px;top:667px;list-style:none;font-family:"Open Sans",sans-serif;font-size:7px;line-height:10px;color:var(--ink)}
  .contact-list li{display:flex;align-items:center;gap:4px;height:10px}
  .contact-list svg{width:8px;height:8px;fill:var(--brand-blue)}
  .office-address{position:absolute;right:54px;top:676px;font-family:"Open Sans",sans-serif;font-size:7px;line-height:9.5px;color:var(--ink);text-align:right}
</style>
</head>
<body>
<div class="canvas">

  <section class="sheet envelope-front" aria-label="Envelope front">
    <div class="band-top"></div>
    <div class="brand-name return-brand">Brighthold Realty</div>
    <p class="return-address">2200 Harbor Crest Way, Suite 140,<br>Lakemont, FL 30000</p>
    <div class="band-bottom"></div>
  </section>

  <section class="sheet envelope-back" aria-label="Envelope back">
    <svg class="flap" width="560" height="100" viewBox="0 0 560 100">
      <path d="M0 0 H560 L548 60 Q542 94 506 94 H54 Q18 94 12 60 Z" fill="var(--brand-blue)"/>
    </svg>
    <div class="flap-brand">Brighthold Realty</div>
  </section>

  <section class="sheet letterhead" aria-label="Letterhead">
    <div class="band-top"></div>
    <div class="brand-name masthead">Brighthold Realty</div>

    <p class="letter letter-date">Cartagena de Indias, Ocober 12,2015</p>
    <p class="letter letter-recipient">Sr.<br>JORGE SALAS<br>Web Master<br>City</p>

    <div class="letter letter-body">
      <p>Contrary to popular belief, Lorem Ipsum is not simply random text. It has roots in a piece of classical Latin literature from 45 BC, making it over 2000 years old. Arthur Linwood, a Latin professor at Westbrook College in Virginia, looked up one of the more obscure Latin words, consectetur, from a Lorem Ipsum passage, and going through the cites of the word in classical literature,</p>
      <p>discovered the undoubtable source. Lorem Ipsum comes from sections 1.10.32 and 1.10.33 of "de Finibus Bonorum et Malorum" (The Extremes of Good and Evil) by Lucian Varro, written in 45 BC. This book is a treatise on the theory of ethics, very popular during the Renaissance. The first line of Lorem Ipsum, "Lorem ipsum dolor sit amet..", comes from a line in section 1.10.32.</p>
      <p>The standard chunk of Lorem Ipsum used since the 1500s is reproduced below for those interested. Sections 1.10.32 and 1.10.33 from "de Finibus Bonorum et Malorum" by Lucian Varro are also reproduced in their exact original form, accompanied by English versions from the 1914 translation by H. Ellery.</p>
      <p>There are many variations of passages of Lorem Ipsum available, but the majority have suffered alteration in some form, by injected humour, or randomised words which don't look even slightly believable. If you are going to use a passage of Lorem Ipsum, you need to be sure there isn't anything embarrassing hidden in the middle of text.</p>
    </div>

    <div class="signature-area" role="img" aria-label="Handwritten signature of the sender"></div>

    <ul class="contact-list">
      <li><svg viewBox="0 0 10 10"><path d="M1 4 Q5 0 9 4 L8 5 L6.5 4 V3 Q5 2.5 3.5 3 V4 L2 5 Z M2.5 6 H7.5 V9 H2.5 Z"/></svg>555-210-4470</li>
      <li><svg viewBox="0 0 10 10"><path d="M3 0.5 H7 V9.5 H3 Z M3.8 1.5 V7.5 H6.2 V1.5 Z"/></svg>555-210-4471</li>
      <li><svg viewBox="0 0 10 10"><path d="M3 1 H7 V4 H3 Z M1 4.5 H9 V9 H1 Z"/></svg>555-210-4472</li>
      <li><svg viewBox="0 0 10 10"><path d="M0.5 2.5 H9.5 V8 H0.5 Z M1 3 L5 6 L9 3"/></svg>office@brightholdrealty.example</li>
    </ul>

    <p class="office-address">2200 Harbor Crest Way, Suite 140,<br>Lakemont, FL 30000<br>www.brightholdrealty.example</p>

    <div class="band-bottom"></div>
  </section>

</div>
</body>
</html>
```